Card and board game developer website, small e-commerce site

We are designing a website for Leaping Otter Engine Works. I need a homepage and a typical inside page designed.
The website navigation will be:
Home (where we'll introduce the games and the website)
Our Games (drops open into the two games)
Griffins of Marrowvale
Tidebound
Order Now
About Us
Contact
The header of the website will include the logo, the navigation and a link to a facebook page. The header will also include a cart icon and a link to My Account.
Then on the homepage I suggest we include a row for each game:
Griffins of Marrowvale
This row will include a photo (or maybe a series of photos that animate into each other) and quick info about the game plus two buttons: Info and Photos (which will go to the detail page with the photo gallery), and Order Now (which will take you to the product for ordering).
Tidebound
Your footer will contain a copyright note, plus links to:
Terms and conditions
Shipping and returns
FAQ
Contact
Account login
NOTE: the logo is the orange mokey. I've uploaded a brief with more information. The current website that we are redesigning is here https://www.leapingotterengine.example/
Please send me any questions that you have.
Target Market(s)
People interested in fun card and board games at home.

```html
<!DOCTYPE html>
<html lang="en">
<head>
<meta charset="utf-8">
<title>About Us – Leaping Otter Engine Works</title>
<link href="https://fonts.googleapis.com/css2?family=Alegreya+Sans:wght@700;800&family=Open+Sans:wght@400;600&display=swap" rel="stylesheet">
<style>
  :root {
    --orange: #f08521;
    --dark: #262223;
    --header-bg: #f8f8f8;
    --ink: #222222;
    --white: #ffffff;
    --ghost: rgba(255,255,255,0.05);
  }
  * { margin: 0; padding: 0; box-sizing: border-box; }
  html, body { width: 1200px; height: 1104px; overflow: hidden; }
  body { position: relative; font-family: "Open Sans", sans-serif; color: var(--ink); background: var(--white); }

  .site-header { position: absolute; top: 0; left: 0; width: 1200px; height: 85px; background: var(--header-bg); z-index: 2; }
  .brand-badge {
    position: absolute; left: 105px; top: -20px; width: 126px; height: 143px;
    border-radius: 0 0 63px 63px; background: var(--header-bg);
    display: flex; align-items: center; justify-content: center; text-align: center;
  }
  .brand-badge span {
    font-family: "Alegreya Sans", sans-serif; font-weight: 800; color: var(--orange);
    font-size: 17px; line-height: 1.05; text-transform: uppercase; margin-top: 18px;
  }
  .main-nav { position: absolute; left: 391px; top: 31px; display: flex; gap: 25px; font-size: 16px; }
  .main-nav a { color: var(--ink); text-decoration: none; }
  .main-nav a.is-current { color: var(--orange); }
  .header-tools { position: absolute; right: 117px; top: 28px; display: flex; gap: 16px; align-items: center; }
  .cart { position: relative; }
  .cart-count {
    position: absolute; right: -4px; top: -6px; width: 17px; height: 17px; border-radius: 50%;
    background: var(--orange); color: var(--ink); font-size: 10px; text-align: center; line-height: 17px;
  }

  .about { position: absolute; top: 85px; left: 0; width: 1200px; height: 744px; background: var(--dark); overflow: hidden; }
  .about-ghost {
    position: absolute; left: 452px; top: 40px; white-space: nowrap;
    font-family: "Alegreya Sans", sans-serif; font-weight: 800; color: var(--ghost);
    font-size: 118px; line-height: 0.95; text-transform: uppercase;
  }
  .about-art {
    position: absolute; left: 111px; top: 102px; width: 385px; height: 547px;
    background: linear-gradient(180deg, #3f63a8 0%, #b8461c 25%, #c9602a 45%, #d9d4cc 62%, #4f7a3a 80%, #3d6a2e 100%);
  }
  .about-copy { position: absolute; left: 542px; top: 105px; width: 560px; color: var(--white); }
  .about-kicker, .about-title { font-family: "Alegreya Sans", sans-serif; font-weight: 800; color: var(--orange); text-transform: uppercase; }
  .about-kicker { font-size: 42px; line-height: 1; }
  .about-title { font-size: 56px; line-height: 1.1; margin-top: 8px; }
  .about-copy p { font-size: 17.5px; line-height: 28px; margin-top: 20px; }
  .about-copy p.lead { margin-top: 28px; }
  .about-copy p.invite { font-weight: 600; margin-top: 22px; }
  .btn-order {
    display: inline-block; margin-top: 52px; margin-left: -3px; width: 140px; height: 47px; line-height: 47px;
    background: var(--orange); color: var(--white); text-align: center; text-decoration: none;
    font-family: "Alegreya Sans", sans-serif; font-weight: 700; font-size: 17px; text-transform: uppercase;
  }

  .site-footer { position: absolute; top: 829px; left: 0; width: 1200px; height: 275px; text-align: center; }
  .footer-brand {
    margin: 55px auto 0; display: flex; align-items: center; justify-content: center; gap: 10px;
    font-family: "Alegreya Sans", sans-serif; font-weight: 800; color: var(--orange); font-size: 22px; text-transform: uppercase;
  }
  .footer-brand i { width: 28px; height: 28px; border-radius: 50%; background: var(--orange); display: block; }
  .footer-links { margin-top: 60px; display: flex; justify-content: center; gap: 28px; font-size: 16px; }
  .footer-links a { color: var(--ink); text-decoration: none; }
  .copyright { margin-top: 14px; font-size: 16px; }
</style>
</head>
<body>
  <header class="site-header">
    <div class="brand-badge"><span>Leaping<br>Otter<br>Engine<br>Works</span></div>
    <nav class="main-nav">
      <a href="#">Home</a>
      <a href="#">Our Games</a>
      <a href="#">Order Now</a>
      <a href="#" class="is-current">About Us</a>
      <a href="#">Contact</a>
    </nav>
    <div class="header-tools">
      <svg width="26" height="26" viewBox="0 0 26 26" aria-label="Social page"><circle cx="13" cy="13" r="11.5" fill="none" stroke="#222" stroke-width="1.6"/></svg>
      <svg width="26" height="26" viewBox="0 0 26 26" aria-label="My account"><circle cx="13" cy="13" r="11.5" fill="none" stroke="#222" stroke-width="1.6"/><circle cx="13" cy="10" r="4" fill="#222"/><path d="M5.5 20.5c2-4 13-4 15 0" fill="#222"/></svg>
      <div class="cart">
        <svg width="30" height="26" viewBox="0 0 30 26" aria-label="Cart"><path d="M1 3h4l3.5 13h15l3-9H7" fill="none" stroke="#222" stroke-width="1.7" stroke-linejoin="round"/><circle cx="11" cy="21" r="2" fill="none" stroke="#222" stroke-width="1.5"/><circle cx="22" cy="21" r="2" fill="none" stroke="#222" stroke-width="1.5"/></svg>
        <span class="cart-count">2</span>
      </div>
    </div>
  </header>

  <section class="about">
    <div class="about-ghost" aria-hidden="true">About Us<br>Leaping Otter<br>Engine Works</div>
    <div class="about-art" role="img" aria-label="Painted game box art: a fire-breathing beast holding cards and gold coins above mountains, castles and a river valley"></div>
    <div class="about-copy">
      <h2 class="about-kicker">About Us</h2>
      <h1 class="about-title">Leaping Otter<br>Engine Works</h1>
      <p class="lead">They say do what you love…</p>
      <p>At Leaping Otter Engine Works we love to dream big dreams and bring those dreams to life. We create games to entertain and engage the people that play them; games that invite and inspire players to add a bit of themselves to each game, and how it is played.</p>
      <p class="invite">Come play with us.</p>
      <a href="#" class="btn-order">Order Now</a>
    </div>
  </section>

  <footer class="site-footer">
    <div class="footer-brand"><i></i>Leaping Otter Engine Works</div>
    <nav class="footer-links">
      <a href="#">Terms and conditions</a>
      <a href="#">Shipping and returns</a>
      <a href="#">FAQ</a>
      <a href="#">Contact</a>
      <a href="#">Account login</a>
    </nav>
    <p class="copyright">2024 Leaping Otter Engine Works. All Rights Reserved.</p>
  </footer>
</body>
</html>
```